Website Re-design for Kids Playhouse Business

Need current website which looks very outdated to be re-designed to look modern and contemporary, reduce clutter significantly and make it look elegant and simple.
Current website: http://www.tumblenest.com.au/
A website which the business owner likes, use as reference/inspiration: http://vexa.com.au/
Looking for light green palette, natural colours. "WHAT'S ON" page/link no longer required.
Industry/Entity Type
Business
Number of Pages Required
5+ page
Look and feel
Each slider illustrates characteristics of the customer's brand and the style your logo design should communicate.

```html
<!DOCTYPE html>
<html lang="en">
<head>
<meta charset="utf-8">
<title>Tumble Nest Playhouse &amp; Cafe</title>
<link href="https://fonts.googleapis.com/css2?family=Kaushan+Script&family=Open+Sans:wght@400;600;700&family=PT+Sans:ital,wght@0,400;0,700;1,400&display=swap" rel="stylesheet">
<style>
:root{
  --lime:#b8d433;
  --ribbon:#a9cc2a;
  --red:#e2231a;
  --orange-bar:rgba(196,98,30,.82);
  --yellow:#f5c400;
  --ink:#333;
  --muted:#999;
  --footer:#1d1b17;
  --white:#fff;
}
*{box-sizing:border-box;margin:0;padding:0}
html,body{width:1200px;height:4337px;overflow:hidden}
body{font-family:"Open Sans",Arial,sans-serif;color:var(--ink);background:var(--white);position:relative}
.section{position:relative;width:1200px;overflow:hidden}
.abs{position:absolute}

/* header + hero */
.hero{height:680px;background:radial-gradient(circle at 65% 35%,#f4d8b0 0,#e6a25c 22%,#3f8a3a 48%,#2a5fa8 70%,#b8262a 100%)}
.hero .photo{position:absolute;inset:0;background:linear-gradient(120deg,rgba(255,190,60,.55),rgba(60,140,200,.35) 50%,rgba(220,40,40,.45))}
.topbar{position:absolute;left:0;top:0;width:1200px;height:108px;background:var(--orange-bar)}
.brand{position:absolute;left:86px;top:42px;width:166px;height:92px;background:var(--white);border-radius:10px;display:flex;align-items:center;justify-content:center;flex-direction:column;gap:2px}
.brand .name{font-weight:700;font-size:21px;color:var(--red);line-height:1}
.brand .sub{font-weight:700;font-size:11px;color:var(--red)}
.nav{list-style:none}
.nav li{position:absolute;top:38px;font-size:13px;font-weight:600;color:var(--white);line-height:18px;text-transform:uppercase;white-space:nowrap}
.nav li.active{color:var(--yellow)}
.hero-title{position:absolute;left:0;width:1200px;top:300px;text-align:center;font-family:"Kaushan Script",cursive;font-weight:400;font-size:62px;color:var(--white);text-shadow:0 3px 6px rgba(0,0,0,.45)}
.ribbon{position:absolute;left:475px;width:250px;height:58px}
.ribbon svg{position:absolute;inset:0}
.ribbon span{position:relative;display:block;text-align:center;line-height:58px;font-size:17px;font-weight:700;color:var(--white);letter-spacing:.5px}

/* about */
.about{height:670px;background:linear-gradient(180deg,#fff 0,#fafafa 38%,#f2d9e8 55%,#f7c9a0 70%,#f0f0f0 100%)}
.about .photo{position:absolute;left:0;top:260px;width:1200px;height:410px;background:linear-gradient(90deg,rgba(230,240,250,.2),rgba(250,170,190,.45) 30%,rgba(255,205,110,.45) 55%,rgba(120,180,230,.3) 80%,rgba(240,240,240,.2))}
.section-title{text-align:center;color:var(--red);font-weight:600;font-size:38px}
.about .section-title{position:absolute;top:58px;width:100%}
.about .lead{position:absolute;top:120px;width:100%;text-align:center;font-size:16px;color:var(--ink)}
.about .copy{position:absolute;top:160px;left:150px;width:900px;text-align:center;font-size:12px;line-height:22px;color:var(--muted)}
.chev{position:absolute;left:571px;top:300px;width:58px;height:58px}

/* green band */
.band{height:170px;background:var(--lime);display:flex;align-items:center;justify-content:center}

/* features */
.features{height:385px;display:flex;gap:6px;background:var(--white)}
.feature{flex:1;position:relative}
.feature .photo{height:315px}
.feature .cap{height:70px;background:var(--lime);color:var(--white);font-size:13.5px;font-weight:600;line-height:18px;padding:17px 40px 0 16px;position:relative}
.feature .cap.hot{background:var(--red)}
.feature .cap svg{position:absolute;right:14px;top:26px}
.f1{background:linear-gradient(135deg,#e94b6f,#f7c04a 55%,#6ab2e4)}
.f2{background:linear-gradient(135deg,#d9c3a8,#a56f4d 50%,#3f3a3a)}
.f3{background:linear-gradient(135deg,#7fc8ec,#e6553d 55%,#2f5f9a)}
.f4{background:linear-gradient(135deg,#6d92b8,#c9a58a 50%,#3e4f63)}

/* testimonial */
.testimonial{height:575px;background:linear-gradient(135deg,#8b8a84,#c7b8a0 40%,#d49a4e 65%,#6d6a62)}
.testimonial .veil{position:absolute;inset:0;background:rgba(255,255,255,.35)}
.quote-box{position:absolute;left:172px;top:188px;width:856px;height:225px;background:rgba(255,255,255,.42)}
.avatar{position:absolute;left:540px;top:125px;width:120px;height:120px;border-radius:50%;background:linear-gradient(135deg,#f4e1cf,#c9a78f);border:6px solid var(--white);box-shadow:0 0 0 3px var(--lime)}
.quote{position:absolute;left:260px;top:272px;width:680px;text-align:center;font-family:"PT Sans",sans-serif;font-style:italic;font-size:16px;line-height:24px;color:var(--ink)}
.quote-by{position:absolute;top:362px;width:100%;text-align:center;color:var(--red);font-family:"PT Sans",sans-serif;font-weight:700;font-size:17px}
.dots{position:absolute;top:495px;left:531px;display:flex;gap:12px}
.dots i{width:12px;height:12px;border-radius:50%;background:var(--white);display:block}
.dots i.on{background:var(--lime)}

/* what we do */
.what{height:590px;background:var(--white)}
.what .section-title{position:absolute;top:70px;width:100%}
.what .photo{position:absolute;left:300px;top:290px;width:600px;height:300px;background:radial-gradient(ellipse at 50% 45%,#f5d3b6 0,#e6b08c 25%,rgba(120,170,220,.55) 50%,rgba(255,255,255,0) 72%)}
.step{position:absolute;width:100px;height:100px}
.step b{position:absolute;inset:0;display:flex;align-items:center;justify-content:center;font-size:48px;font-weight:700;color:var(--ink)}
.step-label{position:absolute;font-size:13px;line-height:19px;color:var(--ink)}

/* photo strip */
.strip{height:740px;background:linear-gradient(90deg,#d9c9a8,#f2ede4 35%,#e9dfd0 55%,#f3f1ee 75%,#cfd7df)}
.strip .photo{position:absolute;inset:0;background:linear-gradient(90deg,rgba(200,60,40,.25),rgba(240,200,60,.2) 25%,rgba(255,255,255,0) 50%,rgba(220,30,40,.35) 85%)}
.arrow{position:absolute;top:346px;width:48px;height:48px;border-radius:50%;background:var(--red);display:flex;align-items:center;justify-content:center}

/* footer */
.footer{height:430px;background:var(--footer);color:#ddd}
.col-title{color:var(--red);font-size:20px;font-weight:600;position:absolute;top:80px}
.footer p{font-size:13px;line-height:21px;color:#ddd}
.contact-row{display:flex;align-items:flex-start;gap:18px;font-size:13px;color:#ddd;margin-bottom:18px}
.social{display:flex;gap:12px;margin-top:4px}
.social i{display:block;width:34px;height:34px;border-radius:50%;background:var(--lime)}
.field{width:330px;height:34px;background:var(--white);margin-bottom:12px;font-size:12px;color:#888;padding:8px 6px}
.field.tall{height:82px}
.btn-ribbon{position:relative;width:160px;height:40px}
.btn-ribbon span{position:relative;display:block;text-align:center;line-height:40px;color:var(--white);font-weight:700;font-size:15px}
.legal{height:67px;background:var(--lime);display:flex;align-items:center;justify-content:center;color:var(--white);font-size:12px;font-weight:600}
</style>
</head>
<body>

<header class="section hero">
  <div class="photo" role="img" aria-label="Photo of a laughing toddler playing in a colourful ball pit"></div>
  <div class="topbar"></div>
  <div class="brand"><span class="name">Tumble Nest</span><span class="sub">Playhouse &amp; Cafe</span></div>
  <ul class="nav">
    <li class="active" style="left:327px">Home</li>
    <li style="left:415px">Hours<br>&amp; Prices</li>
    <li style="left:520px">Party<br>Packages</li>
    <li style="left:635px">Vacation<br>Care</li>
    <li style="left:750px">School<br>Holiday Program</li>
    <li style="left:905px">Specials<br>&amp; Promotions</li>
    <li style="left:1058px">Gallery</li>
  </ul>
  <h1 class="hero-title">So Much Fun For Everyone</h1>
  <div class="ribbon" style="top:400px">
    <svg width="250" height="58" viewBox="0 0 250 58"><polygon points="0,10 18,29 0,48 232,48 250,29 232,10" fill="var(--ribbon)"/><polygon points="18,0 232,0 232,58 18,58" fill="var(--lime)"/></svg>
    <span>JOIN OUR E - CLUB</span>
  </div>
</header>

<section class="section about">
  <div class="photo" role="img" aria-label="Photo of a smiling girl lying on the floor holding colourful toy blocks"></div>
  <h2 class="section-title">About Tumble Nest Playhouse &amp; Cafe</h2>
  <p class="lead">Welcome to Tumble Nest, Sydney's newest and best party &amp; play centre!</p>
  <p class="copy">Tumble Nest is an indoor Kids Play Centre and Cafe that offers both kids and adults a chance to enjoy their time, together! We pride ourselves in offering the best indoor play centre for your kids to engage in fun and learning activities in a specially created environment that is not only warm and safe but also enhances and stimulates creativity and curiosity in a child. Tumble Nest offers variety of kids party packages with our themed party rooms which are hand painted.</p>
  <svg class="chev" viewBox="0 0 58 58"><circle cx="29" cy="29" r="27" fill="var(--white)" stroke="var(--red)" stroke-width="2"/><polyline points="19,22 29,31 39,22" fill="none" stroke="var(--red)" stroke-width="3"/><polyline points="19,30 29,39 39,30" fill="none" stroke="var(--red)" stroke-width="3"/></svg>
</section>

<section class="section band"><h2 class="section-title">Our Features</h2></section>

<section class="section features">
  <div class="feature"><div class="photo f1" role="img" aria-label="Photo of children celebrating a birthday party"></div><div class="cap hot">Perfect venue for<br>birthdays and private parties<svg width="12" height="18"><polygon points="0,0 12,9 0,18" fill="var(--white)"/></svg></div></div>
  <div class="feature"><div class="photo f2" role="img" aria-label="Photo of kids enjoying a themed party room"></div><div class="cap">6 kids loving<br>party rooms themes<svg width="12" height="18"><polygon points="0,0 12,9 0,18" fill="var(--red)"/></svg></div></div>
  <div class="feature"><div class="photo f3" role="img" aria-label="Photo of children cheering at a school holiday program"></div><div class="cap">We host school<br>holiday programs<svg width="12" height="18"><polygon points="0,0 12,9 0,18" fill="var(--red)"/></svg></div></div>
  <div class="feature"><div class="photo f4" role="img" aria-label="Photo of kids climbing a rock wall"></div><div class="cap">Exclusive specials &amp;<br>promotions<svg width="12" height="18"><polygon points="0,0 12,9 0,18" fill="var(--red)"/></svg></div></div>
</section>

<section class="section testimonial">
  <div class="veil" role="img" aria-label="Soft background photo of a child playing"></div>
  <div class="ribbon" style="top:-8px">
    <svg width="250" height="58" viewBox="0 0 250 58"><polygon points="0,10 18,29 0,48 232,48 250,29 232,10" fill="var(--ribbon)"/><polygon points="18,0 232,0 232,58 18,58" fill="var(--lime)"/></svg>
    <span>JOIN OUR E - CLUB</span>
  </div>
  <div class="quote-box"></div>
  <div class="avatar" role="img" aria-label="Reviewer portrait"></div>
  <p class="quote">Love this place, lots of variety for the kids especially in school holidays !! They'll be entertained for hours whilst you enjoy delicious food or a great coffee !! Highly recommend it !!</p>
  <p class="quote-by">— Mara Delphin</p>
  <div class="dots"><i></i><i></i><i class="on"></i><i></i><i></i></div>
</section>

<section class="section what">
  <h2 class="section-title">What We Do</h2>
  <div class="photo" role="img" aria-label="Photo of a grinning boy showing paint-covered hands"></div>

  <div class="step-label" style="left:560px;top:160px;width:80px;text-align:center">Ball Pit</div>
  <div class="step" style="left:550px;top:185px"><svg width="100" height="100"><circle cx="50" cy="50" r="45" fill="#fff" stroke="var(--yellow)" stroke-width="9"/><circle cx="50" cy="50" r="34" fill="none" stroke="#ccc" stroke-width="1.5"/></svg><b>3</b></div>

  <div class="step-label" style="left:80px;top:230px;width:190px;text-align:right">Safe baby play area for 12<br>to 24 months</div>
  <div class="step" style="left:285px;top:215px"><svg width="100" height="100"><circle cx="50" cy="50" r="45" fill="#fff" stroke="var(--red)" stroke-width="9"/><circle cx="50" cy="50" r="34" fill="none" stroke="#ccc" stroke-width="1.5"/></svg><b>2</b></div>

  <div class="step" style="left:785px;top:215px"><svg width="100" height="100"><circle cx="50" cy="50" r="45" fill="#fff" stroke="var(--lime)" stroke-width="9"/><circle cx="50" cy="50" r="34" fill="none" stroke="#ccc" stroke-width="1.5"/></svg><b>4</b></div>
  <div class="step-label" style="left:900px;top:230px;width:210px">Toddler &amp; younger kids<br>play area for 2 to 5 years</div>

  <div class="step-label" style="left:80px;top:410px;width:95px;text-align:right">4 x lane 6m<br>side</div>
  <div class="step" style="left:190px;top:385px"><svg width="100" height="100"><circle cx="50" cy="50" r="45" fill="#fff" stroke="var(--lime)" stroke-width="9"/><circle cx="50" cy="50" r="34" fill="none" stroke="#ccc" stroke-width="1.5"/></svg><b>1</b></div>

  <div class="step" style="left:910px;top:385px"><svg width="100" height="100"><circle cx="50" cy="50" r="45" fill="#fff" stroke="var(--red)" stroke-width="9"/><circle cx="50" cy="50" r="34" fill="none" stroke="#ccc" stroke-width="1.5"/></svg><b>5</b></div>
  <div class="step-label" style="left:1030px;top:410px;width:90px">Rock<br>climbing</div>
</section>

<section class="section strip">
  <div class="photo" role="img" aria-label="Photo of a toddler in a red polka-dot dress beside a wooden abacus"></div>
  <div class="arrow" style="left:18px"><svg width="14" height="18"><polyline points="11,2 3,9 11,16" fill="none" stroke="#fff" stroke-width="3"/></svg></div>
  <div class="arrow" style="right:18px"><svg width="14" height="18"><polyline points="3,2 11,9 3,16" fill="none" stroke="#fff" stroke-width="3"/></svg></div>
</section>

<footer class="section footer">
  <div class="ribbon" style="top:-8px">
    <svg width="250" height="58" viewBox="0 0 250 58"><polygon points="0,10 18,29 0,48 232,48 250,29 232,10" fill="var(--ribbon)"/><polygon points="18,0 232,0 232,58 18,58" fill="var(--lime)"/></svg>
    <span>JOIN OUR E - CLUB</span>
  </div>

  <h3 class="col-title" style="left:80px">About Us</h3>
  <div class="abs" style="left:80px;top:128px;width:310px">
    <p>We welcome all the kids to come and play at our Brookvale indoor play centre. Our kids play centre features slides and lots of other fun activities. We also have a safe toddler area, while you enjoy a cup of coffee and cake, or some lunch from our extensive cafe menu where we only use the freshest "A" grade quality ingredients.</p>
    <div class="btn-ribbon" style="margin-top:14px">
      <svg class="abs" style="inset:0" width="160" height="40" viewBox="0 0 160 40"><polygon points="0,6 12,20 0,34 148,34 160,20 148,6" fill="var(--ribbon)"/><rect x="12" y="0" width="136" height="40" fill="var(--lime)"/></svg>
      <span>READ MORE</span>
    </div>
  </div>

  <h3 class="col-title" style="left:435px">Keep In Touch</h3>
  <div class="abs" style="left:435px;top:135px;width:310px">
    <div class="contact-row"><svg width="16" height="22" viewBox="0 0 16 22"><path d="M8 0a8 8 0 0 0-8 8c0 6 8 14 8 14s8-8 8-14a8 8 0 0 0-8-8z" fill="var(--lime)"/><circle cx="8" cy="8" r="3" fill="var(--footer)"/></svg><span>41 Linden Lane Brookvale 2100 NSW<br>Australia.</span></div>
    <div class="contact-row"><svg width="16" height="18" viewBox="0 0 16 18"><path d="M3 1l3 0 2 4-2 2c1 2 3 4 5 5l2-2 3 2v3c0 1-1 2-2 2C7 17 0 10 0 3c0-1 1-2 3-2z" fill="var(--lime)"/></svg><b style="font-weight:600">02 5550 0142</b></div>
    <div class="contact-row"><svg width="16" height="18" viewBox="0 0 16 18"><rect x="1" y="3" width="14" height="12" rx="1" fill="var(--lime)"/><rect x="4" y="6" width="8" height="4" fill="var(--footer)"/></svg><b style="font-weight:600">02 5550 0187</b></div>
    <div class="contact-row"><svg width="16" height="12" viewBox="0 0 16 12"><rect width="16" height="12" fill="var(--lime)"/><polyline points="0,0 8,7 16,0" fill="none" stroke="var(--footer)" stroke-width="1.5"/></svg><span>hello@tumblenest.example</span></div>
    <div class="social"><i></i><i></i></div>
  </div>

  <h3 class="col-title" style="left:790px">Contact Us</h3>
  <form class="abs" style="left:790px;top:128px">
    <div class="field">Name *</div>
    <div class="field">Email*</div>
    <div class="field">Phone *</div>
    <div class="field tall">Message *</div>
    <div class="btn-ribbon" style="margin-left:85px">
      <svg class="abs" style="inset:0" width="160" height="40" viewBox="0 0 160 40"><polygon points="0,6 12,20 0,34 148,34 160,20 148,6" fill="var(--ribbon)"/><rect x="12" y="0" width="136" height="40" fill="var(--lime)"/></svg>
      <span>SUBMIT</span>
    </div>
  </form>
</footer>

<div class="section legal">©TUMBLE NEST PLAYHOUSE &amp; CAFE - 2018. All rights reserved.</div>

</body>
</html>
```